Quill Press Oceania needs a website

We require a website design which will be different to the normal websites that you visit. The objective of this website will be a call to action on the last page which will link to our email address so customers can email us their quotation requirements.

An example of how we envisage the look and the pages turning is as a flip books for example: https://www.vidharbor.example/watch?v=KtLmPzQa7Rw&feature=vh.be

page 1: just has our logo on it with the tag "Specialist producing quality printed books to your deadline."

Page 2: Black Page with white text "Black and White Book"
These are produced either digitally or offset on a complete range of stocks

Page 3: Colour books (use an image of your choice) These are also produced either digitally or offset plus we have the choice of web presses for larger print runs

Page 4: Digital books We do have a minimum run of 50 books using this process so a one off Thesis is not economically viable using this process. In special circumstance the digital process can produce books more quickly then by using our offset printing process.

Page 5: Having the complete range of printing machines at our disposal enables you to make a perfectly informed choice for your special project.

Then we need a special quote button which takes them directly to our email link. On this page we also need to add: We have had 25 years' experience printing books saving customers time and money whilst guaranteeing quality

Page 6: Logo repeated from page one with name: Morgan Elsworth and mobile phone no 0487 552 314

- Must follow the brief exactly. Must have a turn page book. Clear, simple and concise with a touch of creative flare and must lead into a call for action which is there quotation. A unique button for quotation link...something out of the ordinary which makes someone want to get a quote.

- It would be nice to have 3D Logo on Page 1 & 6.
a unique button for quotation link...something that make someone eager to proceed.

Our main objective is that they should not leave our website without giving us a quote. Please make sure that the spelling is correct and we do not require clip art images. Continue the logo colours through the theme
Updates

here is another example www.vidharbor.example/watch?v=JbXo412TrGe Added Saturday, May 13, 2017

Target Market(s)

Schools, Universities, Self Publishers, Publishers, Graphic Designers, Conference Providers, Businesses, Corporations, Government.

Industry/Entity Type

Printing

Coding

Coded - Design and coding required

Number of Pages Required

5+ page

Font styles to use
Sans Serif

Colors
34a6d7
ec1f27
fbed22
9bcb3c
ffc214
6b449b

Requirements
Must have
• Must follow the brief exactly. Must have a turn page book. Clear, simple and concise with a touch of creative flare and must lead into a call for action which is there quotation. A unique button for quotation link...something out of the ordinary which makes someone want to get a quote. would like to see the colours of the logo use throughout
Nice to have
• 3D Logo on Page 1 & 6.
• a unique button for quotation link...something that make someone eager to proceed.
• Our main objective is that they should not leave our website without giving us a quote
Should not have
• Spelling mistakes, clip art, ordinary design

```html
<!DOCTYPE html>
<html lang="en">
<head>
<meta charset="utf-8">
<title>Quill Press Oceania – Colour Books</title>
<link href="https://fonts.googleapis.com/css2?family=Roboto:wght@700&family=Roboto+Condensed:wght@300;400&display=swap" rel="stylesheet">
<style>
  :root {
    --ink: #333333;
    --page-light: #ffffff;
    --page-edge: #e6e6e6;
    --brand-blue: #34a6d7;
    --brand-red: #ec1f27;
    --brand-yellow: #fbed22;
    --brand-green: #9bcb3c;
    --brand-amber: #ffc214;
    --brand-purple: #6b449b;
    --book-pink: #e8356f;
    --book-orange: #ffa514;
  }
  html, body {
    margin: 0;
    padding: 0;
    overflow: hidden;
  }
  .page {
    position: relative;
    width: 720px;
    height: 1200px;
    overflow: hidden;
    background: radial-gradient(ellipse at 50% 45%, var(--page-light) 0%, #f7f7f7 55%, var(--page-edge) 100%);
    font-family: "Roboto Condensed", "Arial Narrow", sans-serif;
    color: var(--ink);
  }
  .ornament {
    position: absolute;
  }
  .ornament--top {
    left: 0;
    top: 0;
    width: 512px;
    height: 344px;
    border-bottom-right-radius: 100% 100%;
    background: radial-gradient(circle at 22% 18%, var(--brand-red) 0%, var(--book-orange) 22%, var(--brand-amber) 38%, var(--brand-blue) 62%, rgba(52,166,215,0.25) 82%, rgba(255,255,255,0) 100%);
  }
  .ornament--bottom {
    right: 0;
    bottom: 0;
    width: 536px;
    height: 464px;
    border-top-left-radius: 100% 100%;
    background: radial-gradient(circle at 78% 82%, var(--brand-red) 0%, var(--brand-amber) 16%, var(--brand-green) 34%, var(--brand-blue) 54%, rgba(200,200,200,0.35) 78%, rgba(255,255,255,0) 100%);
  }
  .book-stack {
    position: absolute;
    left: 228px;
    top: 216px;
    width: 368px;
    height: 304px;
    border-radius: 24px;
    background: linear-gradient(180deg, var(--book-orange) 0%, var(--brand-amber) 30%, var(--brand-blue) 55%, var(--book-pink) 100%);
  }
  .heading {
    position: absolute;
    left: 0;
    top: 570px;
    width: 720px;
    margin: 0;
    text-align: center;
    font-family: "Roboto", Arial, sans-serif;
    font-weight: 700;
    font-size: 36px;
    line-height: 44px;
    letter-spacing: 0.5px;
    color: var(--ink);
  }
  .description {
    position: absolute;
    left: 0;
    top: 634px;
    width: 720px;
    margin: 0;
    text-align: center;
    font-weight: 300;
    font-size: 33px;
    line-height: 52px;
    text-transform: uppercase;
    color: var(--ink);
  }
  .page-number {
    position: absolute;
    left: 8px;
    bottom: 6px;
    font-family: "Roboto", Arial, sans-serif;
    font-size: 12px;
    color: var(--ink);
  }
</style>
</head>
<body>
  <main class="page">
    <div class="ornament ornament--top" role="img" aria-label="Colourful hand-drawn floral doodle in red, orange, yellow and blue"></div>
    <div class="ornament ornament--bottom" role="img" aria-label="Colourful and line-art paisley floral doodle in green, yellow, pink and blue"></div>
    <div class="book-stack" role="img" aria-label="Stack of three books in orange, blue and pink with a bookmark"></div>

    <h1 class="heading">COLOUR BOOKS</h1>
    <p class="description">
      These are also produced<br>
      either digitally or offset plus we<br>
      have the choice of web presses<br>
      for larger print runs
    </p>

    <span class="page-number">C7</span>
  </main>
</body>
</html>
```